Barrister at Law needs Business Card Design

Need a business card design for Barrister at Law. Double sided. Simple Neil Thorsby and Barrister at Law on one side with contact details on the other side. I would like a professional design using Black or Platinum. Details on reverse side would include qualifications - Bcom-Llb and Acc Spec Commercial Litigation. I have attached the logo. Contact details would include address/ Po Box/ Phone/Fax/Mobile/email. I would like to use raised print or spot gloss.

```html
<!DOCTYPE html>
<html lang="en">
<head>
<meta charset="utf-8">
<title>Neil Thorsby – Barrister-at-Law Business Card</title>
<link href="https://fonts.googleapis.com/css2?family=Cinzel:wght@400;500&family=Source+Sans+3:wght@400;600&display=swap" rel="stylesheet">
<style>
  :root {
    --backdrop: #4a4341;
    --card: #1c1d1f;
    --card-edge: #141416;
    --blue: #1f76c2;
    --blue-dark: #15558f;
    --platinum: #c9ccd0;
    --silver: #9a9ea3;
    --text-light: #e8e9eb;
  }
  * { box-sizing: border-box; margin: 0; padding: 0; }
  html, body { width: 1200px; height: 814px; overflow: hidden; background: var(--backdrop); }
  .canvas { position: relative; width: 1200px; height: 814px; }
  .card {
    position: absolute; top: 264px; width: 500px; height: 286px;
    background: var(--card); overflow: hidden;
    box-shadow: 0 10px 24px rgba(0,0,0,.45);
  }
  .card--front { left: 70px; }
  .card--back { left: 630px; }

  .front-name {
    position: absolute; left: 0; right: 0; top: 104px; text-align: center;
    font-family: "Cinzel", serif; font-size: 30px; font-weight: 500;
    color: var(--blue); letter-spacing: 1px;
  }
  .front-title {
    position: absolute; left: 0; right: 0; top: 144px; text-align: center;
    font-family: "Cinzel", serif; font-size: 20px;
    color: var(--silver); letter-spacing: 1.5px;
  }

  .back-bands { position: absolute; inset: 0; }
  .brand {
    position: absolute; left: 70px; top: 96px; width: 150px;
    display: flex; align-items: center; gap: 10px;
    font-family: "Source Sans 3", sans-serif; font-weight: 600; font-size: 17px;
    color: var(--platinum);
  }
  .brand-dot { width: 12px; height: 12px; border-radius: 50%; background: var(--platinum); flex: none; }
  .divider {
    position: absolute; left: 240px; top: 62px; width: 1px; height: 118px;
    background: #55585c;
  }
  .contact {
    position: absolute; left: 258px; top: 66px;
    font-family: "Source Sans 3", sans-serif; font-size: 13px; line-height: 17px;
    color: var(--text-light); list-style: none;
  }
  .contact-address { margin-bottom: 4px; }
  .contact-row { display: flex; align-items: center; gap: 8px; }
  .contact-row svg { width: 12px; height: 12px; flex: none; }
  .contact-email { margin-top: 4px; }
  .website {
    position: absolute; right: 28px; bottom: 8px;
    font-family: "Source Sans 3", sans-serif; font-size: 15px;
    color: var(--text-light); letter-spacing: 3px;
  }
</style>
</head>
<body>
<main class="canvas">
  <section class="card card--front" aria-label="Card front">
    <h1 class="front-name">NEIL THORSBY</h1>
    <p class="front-title">BARRISTER-AT-LAW</p>
  </section>

  <section class="card card--back" aria-label="Card back">
    <svg class="back-bands" viewBox="0 0 500 286" width="500" height="286">
      <polygon points="0,172 0,186 228,252 246,252" fill="var(--platinum)"/>
      <polygon points="0,186 0,286 500,286 500,250 246,250 228,252" fill="var(--blue)"/>
      <polygon points="0,192 0,200 226,258 240,256" fill="var(--blue-dark)" opacity=".5"/>
    </svg>

    <div class="brand"><span class="brand-dot"></span><span>Thorsby Law</span></div>
    <div class="divider"></div>

    <ul class="contact">
      <li class="contact-address">214 Wexley Row<br>Harlow Bay, Dunmore 20817</li>
      <li class="contact-row">
        <svg viewBox="0 0 12 12"><path d="M2.5 1 L4.5 1 L5.3 3.5 L4 4.6 C4.8 6.2 5.8 7.2 7.4 8 L8.5 6.7 L11 7.5 L11 9.5 C11 10.3 10.3 11 9.5 11 C5 10.7 1.3 7 1 2.5 C1 1.7 1.7 1 2.5 1 Z" fill="var(--blue)"/></svg>
        <span>612 508 3941</span>
      </li>
      <li class="contact-row">
        <svg viewBox="0 0 12 12"><rect x="3" y="0.5" width="6" height="11" rx="1" fill="none" stroke="var(--blue)" stroke-width="1.2"/><circle cx="6" cy="9.6" r=".7" fill="var(--blue)"/></svg>
        <span>745 219 6083</span>
      </li>
      <li class="contact-row">
        <svg viewBox="0 0 12 12"><rect x="3" y="1" width="6" height="3" fill="var(--blue)"/><rect x="1" y="4.5" width="10" height="6.5" rx="1" fill="var(--blue)"/></svg>
        <span>390 742 1657</span>
      </li>
      <li class="contact-row contact-email">
        <svg viewBox="0 0 12 12"><rect x="0.5" y="2" width="11" height="8" fill="var(--blue)"/><path d="M0.5 2 L6 6.5 L11.5 2" fill="none" stroke="var(--card)" stroke-width="1"/></svg>
        <span>clerk@thorsbylaw.net</span>
      </li>
    </ul>

    <p class="website">www.thorsbylaw.net</p>
  </section>
</main>
</body>
</html>
```